Website redesign for job agency recruitment

Please refer to the attached document, “Tarvenly Work Website Brief,” for comprehensive details regarding the scope, objectives, and requirements of this website redesign project.

For imagery you can use images from this website https://www.pixelmarrowfoto.com or any other you regularly use.

Target Market(s)

Jobseekers and Companies looking for general labour

Industry/Entity Type

Services: Oil, Gas and Mining, Administrative, Construction and Trades, Warehouse and Logistics and, Manufacturing.

Number of Pages Required

5+ page

Font styles to use
Serif
Other font styles liked:
• Inter, Open-Sans or similar.

Requirements
Must have
• The requirements highlighted in the Word document attached. The final design needs to be provided in Figma including all viewports (Desktop, mobiel and tablet)
Should not have
• Website we like as a reference: www.brevicktalentco.com, www.qelvaworks.com, www.zunmarra.com, www.ferrowhires.com, www.9vtalentpool.com, www.hiringwithtrello.ca

```html
<!DOCTYPE html>
<html lang="en">
<head>
<meta charset="utf-8">
<title>Tarvenly Work Agency</title>
<link href="https://fonts.googleapis.com/css2?family=Barlow:wght@700;800&family=Open+Sans:wght@400;600;700&display=swap" rel="stylesheet">
<style>
:root{
  --navy:#12284b;
  --yellow:#f6bf1a;
  --ink:#1c1c1c;
  --muted:#555;
  --white:#fff;
}
*{margin:0;padding:0;box-sizing:border-box}
html,body{width:1200px;height:2259px;overflow:hidden;background:var(--white)}
body{position:relative;font-family:"Open Sans",sans-serif;color:var(--ink)}
.abs{position:absolute}

/* header */
.site-header{position:absolute;top:0;left:0;width:1200px;height:91px;background:var(--white);border-top:3px solid var(--yellow);z-index:5}
.nav a{position:absolute;top:56px;font-size:15px;color:var(--ink);text-decoration:none}
.nav a.active{color:var(--yellow)}
.toll{position:absolute;top:17px;right:143px;font-size:13px;color:#555;display:flex;align-items:center;gap:6px}
.logo-cap{position:absolute;left:498px;top:0;width:204px;height:120px;background:var(--white);border-radius:0 0 102px 102px;z-index:6;display:flex;flex-direction:column;align-items:center;justify-content:center;padding-top:6px}
.brand{display:flex;align-items:center;gap:6px;font-weight:700;color:var(--navy);font-size:28px;line-height:1}
.brand .dot{width:14px;height:14px;border-radius:50%;background:var(--yellow)}
.brand-sub{font-size:9.5px;color:var(--navy);font-weight:600;margin-top:6px}

/* hero */
.hero{position:absolute;top:91px;left:0;width:1200px;height:601px;background:linear-gradient(180deg,#6fa6cf 0%,#a9c5cf 22%,#d8c98e 30%,#7f8b93 42%,#5a646d 70%,#3d4650 100%)}
.hero h1{position:absolute;top:140px;left:0;width:1200px;text-align:center;font-family:"Barlow",sans-serif;font-weight:700;font-size:57px;line-height:68px;color:var(--white);letter-spacing:.5px}
.hero p{position:absolute;top:226px;left:0;width:1200px;text-align:center;font-size:18px;line-height:24px;color:var(--white)}
.btn{position:absolute;display:flex;align-items:center;justify-content:center;border-radius:26px;font-weight:700;font-size:16px;letter-spacing:.3px;text-decoration:none}
.btn-yellow{background:var(--yellow);color:var(--navy)}
.btn-white{background:var(--white);color:var(--ink)}

/* services */
.services-title{position:absolute;left:143px;top:852px;font-family:"Barlow",sans-serif;font-weight:700;font-size:36px;line-height:56px;color:var(--ink)}
.services-text{position:absolute;left:143px;top:965px;width:195px;font-size:14px;line-height:23.3px;color:var(--muted)}
.svc{position:absolute;font-size:17px;color:var(--ink)}
.svc.active{color:var(--yellow)}
.svc-card{position:absolute;left:718px;top:854px;width:336px;height:336px;border-radius:50%;background:var(--navy);color:var(--white);text-align:center;padding:72px 34px 0}
.svc-card h3{font-weight:400;font-size:20px;margin-bottom:10px}
.svc-card p{font-size:13.5px;line-height:23.3px}
.svc-card .more{display:block;margin-top:16px;color:var(--yellow);font-weight:700;font-size:15px}
.photo{position:absolute;border-radius:50%}

/* about */
.about{position:absolute;top:1306px;left:0;width:1200px;height:612px;background:var(--navy)}
.about h2{position:absolute;left:630px;top:136px;font-family:"Barlow",sans-serif;font-weight:700;font-size:38px;color:var(--white)}
.about .tag{position:absolute;left:630px;top:194px;font-size:13px;color:var(--yellow)}
.about .copy{position:absolute;left:630px;top:226px;width:428px;color:var(--white);font-size:13.6px;line-height:23.3px;text-align:justify}
.about .copy p+p{margin-top:9px}

/* footer */
.footer-brand{position:absolute;top:1925px;left:0;width:1200px;display:flex;flex-direction:column;align-items:center}
.footer-brand .brand{font-size:44px}
.footer-brand .brand .dot{width:20px;height:20px}
.footer-brand .name{font-size:16px;font-weight:600;color:var(--navy);margin-top:14px}
.footer-brand .line{font-size:10px;color:#777;margin-top:3px}
.footer-nav{position:absolute;top:2096px;left:0;width:1200px;display:flex;justify-content:center;gap:36px;font-size:15px;color:var(--ink)}
.footer-rule{position:absolute;top:2141px;left:150px;width:900px;height:1px;background:#e6e6e6}
.copyright{position:absolute;top:2164px;left:0;width:1200px;text-align:center;font-size:14px;color:var(--ink)}
.social{position:absolute;top:2196px;left:568px;display:flex;gap:6px}
.social span{width:26px;height:26px;border-radius:50%;border:1px solid #ddd;background:var(--white)}
.social span.on{background:var(--yellow);border-color:var(--yellow)}
</style>
</head>
<body>

<header class="site-header">
  <nav class="nav">
    <a class="active" style="left:143px">Home</a>
    <a style="left:225px">Candidates</a>
    <a style="left:343px">Companies</a>
    <a style="left:761px">About Us</a>
    <a style="left:865px">Contact</a>
    <a style="left:959px">Forms &amp; Links</a>
  </nav>
  <div class="toll">
    <svg width="11" height="11" viewBox="0 0 24 24"><path fill="#12284b" d="M6.6 10.8a15.1 15.1 0 0 0 6.6 6.6l2.2-2.2c.3-.3.7-.4 1-.2 1.1.4 2.3.6 3.6.6.6 0 1 .4 1 1V20c0 .6-.4 1-1 1A17 17 0 0 1 3 4c0-.6.4-1 1-1h3.5c.6 0 1 .4 1 1 0 1.3.2 2.5.6 3.6.1.3 0 .7-.2 1z"/></svg>
    Toll Free 1-888-555-0142
  </div>
</header>
<div class="logo-cap">
  <div class="brand"><span class="dot"></span>TWA</div>
  <div class="brand-sub">Tarvenly Work Agency Ltd.</div>
</div>

<section class="hero" role="img" aria-label="Aerial photo of a city skyline with skyscrapers at sunrise">
  <h1>OUR GOAL IS YOUR SUCCESS</h1>
  <p>Tarvenly Work Agency offer various opportunities in the different industries.</p>
  <a class="btn btn-yellow" style="left:396px;top:283px;width:200px;height:52px">FOR CANDIDATES</a>
  <a class="btn btn-white" style="left:604px;top:283px;width:200px;height:52px">FOR EMPLOYERS</a>
  <svg class="abs" style="left:0;top:489px" width="1200" height="112" viewBox="0 0 1200 112">
    <path fill="#f6bf1a" d="M0,12 C150,72 350,106 510,112 L0,112Z"/>
    <path fill="#12284b" d="M1200,12 C1050,72 850,106 690,112 L1200,112Z"/>
    <path fill="#fff" d="M0,42 C220,96 420,112 600,112 C780,112 980,96 1200,42 L1200,112 L0,112Z"/>
  </svg>
</section>

<!-- services -->
<svg class="abs" style="left:0;top:760px" width="400" height="480" viewBox="0 0 400 480">
  <path d="M143,13 A225,225 0 0 1 298,73" fill="none" stroke="#f6bf1a" stroke-width="7"/>
  <path d="M298,73 A225,225 0 0 1 143,457" fill="none" stroke="#12284b" stroke-width="7"/>
</svg>
<h2 class="services-title">OUR<br>SERVICES</h2>
<p class="services-text">With specialist divisions immersed into the heartbeat of five industries, we are the "go to" people who screen, interview, and successfully manage thousands of relationships each day.</p>
<span class="svc active" style="left:294px;top:772px">Gas and Mining</span>
<span class="svc" style="left:383px;top:859px">Administrative</span>
<span class="svc" style="left:430px;top:942px">Construction and Trade</span>
<span class="svc" style="left:431px;top:1025px">Warehouse and Logistics</span>
<span class="svc" style="left:381px;top:1111px">Manufacturing</span>
<span class="svc" style="left:294px;top:1198px">Oil</span>

<div class="photo" role="img" aria-label="Photo of two workers in hard hats at an oil pump site" style="left:968px;top:708px;width:215px;height:215px;background:linear-gradient(160deg,#6f8fc4,#a7b8c9 55%,#7a6a55)"></div>
<div class="photo" role="img" aria-label="Photo of an engineer with a laptop near drilling equipment" style="left:1075px;top:949px;width:154px;height:154px;background:linear-gradient(160deg,#4f88c8,#9fc0df 60%,#6c6a60)"></div>
<div class="photo" role="img" aria-label="Photo of a drilling rig with pipes and workers" style="left:905px;top:1068px;width:215px;height:215px;background:linear-gradient(160deg,#8fa9c4,#536377 55%,#4a4a4a)"></div>
<div class="svc-card">
  <h3>Gas and Mining</h3>
  <p>Sed ut perspiciatis unde omnis iste natus error sit voluptatem accusantium doloremque laudantium, totam rem aperiam, eaque ipsa quae ab illo inven-tore veritatis et quasi</p>
  <span class="more">LEARN MORE &#8250;</span>
</div>

<!-- about -->
<section class="about">
  <svg class="abs" style="left:0;top:0" width="1200" height="90" viewBox="0 0 1200 90">
    <path fill="#fff" d="M0,0 H1200 V2 Q600,162 0,2Z"/>
    <path fill="none" stroke="#f6bf1a" stroke-width="7" d="M140,18 Q600,126 1060,18"/>
  </svg>
  <div class="photo" role="img" aria-label="Photo of three business people meeting at an office table" style="left:145px;top:93px;width:420px;height:420px;background:linear-gradient(135deg,#e8eef2,#c7d3dc 45%,#2c3e5a 80%)"></div>
  <h2>ABOUT TARVENLY WORK</h2>
  <p class="tag">Tarvenly Work Agency. The right people to power your business!</p>
  <div class="copy">
    <p>Tarvenly Work Agency offers a complete range of staffing services to keep pace with your career or operational demands. We understand it's not only daunting but very costly in both time and money to make your business thrive in a rapidly changing environment.</p>
    <p>Our staffing and recruitment services are not just limited to finding good people. We are a Canada-wide team of capable search special-ists, career counselors, HR specialists, and business</p>
  </div>
  <a class="btn btn-yellow" style="left:630px;top:427px;width:144px;height:44px;font-size:15px">READ MORE</a>
  <svg class="abs" style="left:0;top:512px" width="1200" height="100" viewBox="0 0 1200 100">
    <path fill="#fff" d="M0,100 L0,98 Q600,-44 1200,98 L1200,100Z"/>
    <path fill="none" stroke="#f6bf1a" stroke-width="8" d="M60,100 Q600,-22 1140,100"/>
  </svg>
</section>

<footer>
  <div class="footer-brand">
    <div class="brand"><span class="dot"></span>TWA</div>
    <div class="name">Tarvenly Work Agency Ltd.</div>
    <div class="line">The right people to power your business</div>
  </div>
  <nav class="footer-nav">
    <span>HOME</span><span>|</span><span>CANDIDATES</span><span>|</span><span>COMPANIES</span><span>|</span><span>ABOUT US</span><span>|</span><span>CONTACT</span><span>|</span><span>FORMS &amp; LINKS</span>
  </nav>
  <div class="footer-rule"></div>
  <p class="copyright">© 2026 Tarvenly Work Agency Ltd - &nbsp;Terms of Use</p>
  <div class="social" aria-label="Social links">
    <span aria-label="Social profile"></span><span class="on" aria-label="Social profile"></span>
  </div>
</footer>

</body>
</html>
```